Business card for Sports Apparel business

DOUBLE SIDED DESIGN
We need business cards for a new sports apparel business. We are developing a protective headband for soccer initially.
Torvalle is focused on designing and developing head protection products to reduce the likelihood of concussion when playing sports. Exploring and understanding medical insights, material science research, current and former players experiences and governing bodies guidelines has allowed Torvalle to develop the safety, style, form and function requirements of a suitable product to bring to market.
Target Market(s)
Mums buying kits for the sons and daughters. Amateur footballers.
Industry/Entity Type
Sporting Good
Contact Information for Business Card
Martin Ashworth - CEO
Mobile: +44 7431589027
Email: martin@torvalle.co.uk
Tel: 0208 5519372
Helena Pargeter - COO
Mob: +44 7385 640117
Email: helena@torvalle.co.uk
Tel: 0208 5519372
Duncan Farrow - CCO
Mob: +44 7564 293081
Email: duncan@torvalle.co.uk
Tel: 0208 5519372
Look and feel
Each slider illustrates characteristics of the customer's brand and the style your logo design should communicate.

```html
<!DOCTYPE html>
<html lang="en">
<head>
<meta charset="utf-8">
<title>Torvalle Business Card</title>
<link href="https://fonts.googleapis.com/css2?family=Montserrat:wght@500;700&family=Arimo:wght@400&display=swap" rel="stylesheet">
<style>
  :root {
    --backdrop: #2b2b2b;
    --card-white: #ffffff;
    --brand-blue: #0d5a96;
    --text-grey: #4a4a4a;
    --text-dark: #1f1f1f;
    --rule-grey: #8a8a8a;
    --pitch-teal: #1f7f96;
    --pitch-teal-light: #3a97a8;
    --pitch-teal-dark: #176c86;
  }
  * { margin: 0; padding: 0; box-sizing: border-box; }
  html, body { width: 1200px; height: 1200px; overflow: hidden; }
  body { background: var(--backdrop); position: relative; }

  .card {
    position: absolute;
    top: 310px;
    height: 594px;
  }
  .card-front {
    left: 234px;
    width: 364px;
    background: var(--card-white);
  }
  .card-back {
    left: 627px;
    width: 370px;
    background: linear-gradient(160deg, var(--pitch-teal-dark) 0%, var(--pitch-teal-light) 30%, var(--pitch-teal) 60%, var(--pitch-teal-dark) 100%);
  }

  .brand-name {
    position: absolute;
    left: 0;
    width: 100%;
    text-align: center;
    font-family: 'Montserrat', sans-serif;
    font-weight: 500;
    font-size: 40px;
    letter-spacing: 1px;
    line-height: 1;
  }
  .card-front .brand-name { top: 163px; color: var(--brand-blue); }
  .card-back .brand-name { top: 277px; color: var(--card-white); }

  .holder-name {
    position: absolute;
    top: 373px;
    width: 100%;
    text-align: center;
    font-family: 'Montserrat', sans-serif;
    font-weight: 700;
    font-size: 20px;
    color: var(--brand-blue);
  }
  .holder-role {
    position: absolute;
    top: 400px;
    width: 100%;
    text-align: center;
    font-family: 'Arimo', sans-serif;
    font-size: 17px;
    color: var(--text-grey);
  }

  .contact-icons {
    position: absolute;
    top: 446px;
    left: 87px;
    width: 190px;
    height: 24px;
    display: flex;
    align-items: center;
    justify-content: center;
    gap: 5px;
  }
  .contact-icons .rule {
    flex: 1;
    height: 1px;
    background: var(--rule-grey);
  }
  .contact-icons .rule:first-child { margin-right: 4px; }
  .contact-icons .rule:last-child { margin-left: 4px; }
  .contact-icons svg { width: 24px; height: 24px; display: block; }

  .contact-lines {
    position: absolute;
    top: 482px;
    width: 100%;
    text-align: center;
    font-family: 'Arimo', sans-serif;
    font-size: 16.5px;
    line-height: 22px;
    color: var(--text-dark);
    list-style: none;
  }
</style>
</head>
<body>
  <section class="card card-front">
    <div class="brand-name">TORVALLE</div>
    <h1 class="holder-name">MARTIN ASHWORTH</h1>
    <p class="holder-role">CEO</p>
    <div class="contact-icons">
      <span class="rule"></span>
      <svg viewBox="0 0 24 24" aria-label="Telephone">
        <rect width="24" height="24" rx="2" fill="var(--brand-blue)"/>
        <path d="M5 10 Q12 5 19 10 L17 12 L15 10.5 L9 10.5 L7 12 Z" fill="#fff"/>
        <rect x="7" y="12" width="10" height="6" rx="1" fill="#fff"/>
        <circle cx="12" cy="15" r="1.6" fill="var(--brand-blue)"/>
      </svg>
      <svg viewBox="0 0 24 24" aria-label="Mobile">
        <rect width="24" height="24" rx="2" fill="var(--brand-blue)"/>
        <rect x="7.5" y="5" width="9" height="14" rx="1.5" fill="none" stroke="#fff" stroke-width="1.6"/>
        <circle cx="12" cy="16.5" r="0.9" fill="#fff"/>
      </svg>
      <svg viewBox="0 0 24 24" aria-label="Email">
        <rect width="24" height="24" rx="2" fill="var(--brand-blue)"/>
        <rect x="5" y="7.5" width="14" height="9.5" fill="none" stroke="#fff" stroke-width="1.5"/>
        <path d="M5 7.5 L12 13 L19 7.5 M5 17 L10 12 M19 17 L14 12" fill="none" stroke="#fff" stroke-width="1.3"/>
      </svg>
      <span class="rule"></span>
    </div>
    <ul class="contact-lines">
      <li>0208 5519372</li>
      <li>+44 7431589027</li>
      <li>martin@torvalle.co.uk</li>
    </ul>
  </section>

  <section class="card card-back" role="img" aria-label="Aerial photograph of a football pitch in a teal tone">
    <div class="brand-name">TORVALLE</div>
  </section>
</body>
</html>
```